Maple Lantern Productions web site

I need to build a website for a new company I am launching next month. Maple Lantern Productions is a company based in New England that provides sound, lighting, and audio visual services to weddings, corporate, and any other cusomer base looking for quality service for a fair price. Looking for somebody to do a full site not just the image files. I am looking to keep the colors of my logo (orange and black) and possibly grey and white. I am looking to build my site very similar to brightvaleevents.example, which is owned by a friend of mine. I like how he has the big pictures that load in to the site and the basic menu items. I'll need a gallery of photos. The designs should communicate quality, value and trust.
My website address is maplelanternco.example.
Updates

Hi and thanks to everyone for posting such great ideas for our new design.I have some items that I'd like to ask you all to focus on in your revisions.I like how http://www.brightvaleevents.example/ website has five or six high res pictures that change in a slideshow format with a caption that loads in for each one for the different types of services. Try and capture pics like these and with teh same headings as he has. The basic menu designs have been interesting.I am more fond of the menus that are more white with some orange as I dont want it to be too dark. I'm curious to see how your galleries will work and if i'll be able to edit the pages myself? I have some more info on the company for you to fill in:website address is ciderhouseco.comemail: info@ciderhouseco.comaddress: Maple Lantern Productions57 Littlefield StreetAvon, MA 02417"New England's finest DJ's, lighting and sound, video and more. Creating memories one perfect event at a time."Put this under the loading pictures as a tagline.About Cider HouseCider House Productions is a collection of New England's finest talent, ready to make your next event the one you've dreamed of. We have the skills and expertise to deliver your vision of your perfect event. From elegant weddings to themed mitzvah's, corporate av, videography and detail lighting, we offer all of the elements to make your event a success. Added Wednesday, March 1, 2017

Designer's Please also make sure that your design flows well on any device it is being viewed on as well. Thanks. Added Wednesday, March 1, 2017

Project Deadline Extended Reason: Hello designerThank you all very much for your hard work on our project. Im sorry but i need to extend the date of my project. Our parent conpany Rook Nine Prodactions sponsors Bay Youth Assemblies and we are currently at their leadership conference on the Cape. I will be back in on Monday and with your help will get this finished by Thursday the 16th. Thanks Added Thursday, March 9, 2017

Project Deadline Extended Reason: One of the designers is not responding so I now have to make revisions with other designers. I hope to get this website done over the weekends so please get your revisions as soon as possible. Thank you. I am also upgrading the budget another $75 to hopefully get some more interest on my project. Added Wednesday, March 15, 2017

Target Market(s)

Wedding - Corporate -

Industry/Entity Type

It Company

Coding

Coded - Design and coding required

Number of Pages Required

5+ page

Font styles to use
Sans Serif

Requirements
Must have
• Photo Gallery - I want to be able to edit it myself
Nice to have
• I like the look of my friends website brightvaleevents.example

```html
<!DOCTYPE html>
<html lang="en">
<head>
<meta charset="utf-8">
<title>Maple Lantern Productions</title>
<link rel="stylesheet" href="https://fonts.googleapis.com/css2?family=Montserrat:wght@400;600;700&family=Questrial&display=swap">
<style>
:root{
  --orange:#f05a28;
  --ink:#1d1d1d;
  --text:#444;
  --muted:#8a8a8a;
  --light:#ececec;
  --footer:#222;
  --footer-bar:#1a1a1a;
  --white:#fff;
  --client:#555;
}
*{margin:0;padding:0;box-sizing:border-box}
html,body{width:1200px;height:4775px;overflow:hidden}
body{font-family:"Questrial",sans-serif;color:var(--text);background:var(--white);position:relative}
.abs{position:absolute}
.heading{font-family:"Montserrat",sans-serif;font-weight:700;color:var(--ink);text-transform:uppercase;text-align:center}
.center{left:0;width:1200px;text-align:center}

/* nav */
.site-nav{top:0;left:0;width:1200px;height:90px;background:var(--white)}
.brand{left:162px;top:22px;display:flex;align-items:center;gap:10px}
.brand-dot{width:40px;height:40px;border-radius:50%;background:var(--orange)}
.brand-name{font-family:"Montserrat",sans-serif;font-weight:700;font-size:17px;color:var(--ink);line-height:1.05}
.brand-name small{display:block;font-size:10px;letter-spacing:3px;font-weight:700}
.menu{top:36px;left:436px;display:flex;gap:38px;font-size:15px;color:var(--ink);font-family:"Montserrat",sans-serif}
.menu .sep{width:1px;height:22px;background:#ccc;margin-top:-2px}
.search{top:36px;left:1020px}

/* hero */
.hero{top:90px;left:0;width:1200px;height:522px;background:radial-gradient(circle at 30% 25%,#6d7fb8 0,#2c2436 30%,#140f14 70%),#140f14}
.hero-photo{position:absolute;inset:0;background:radial-gradient(ellipse at 55% 45%,rgba(230,225,230,.35),transparent 40%),radial-gradient(circle at 88% 55%,rgba(200,140,80,.35),transparent 30%)}
.hero-title{top:186px;font-family:"Montserrat",sans-serif;font-weight:700;font-size:62px;color:var(--white)}
.hero-sub{top:268px;font-size:17px;color:var(--white);letter-spacing:.5px;text-transform:uppercase}
.btn{display:inline-block;background:var(--orange);color:var(--white);font-family:"Montserrat",sans-serif;font-weight:600;text-transform:uppercase;border-radius:24px}
.hero-btn{top:305px;left:519px;width:251px;height:45px;line-height:45px;font-size:15px;text-align:center}
.arrow{top:235px}

/* intro */
.intro-title{top:650px;font-size:38px}
.intro-title span{color:var(--orange)}
.lead{font-size:17px;line-height:1.6;color:var(--text);text-align:center}
.intro-lead{top:716px;left:270px;width:660px}
.photo{position:absolute}
.card-title{font-size:18px;color:var(--orange);text-align:center}
.card-text{font-size:12px;line-height:1.55;text-align:center;color:var(--text)}

/* bands */
.band{left:0;width:1200px;height:206px}
.band-title{font-size:36px;color:var(--white)}
.band-sub{font-size:17px;color:#ddd}
.notch{left:570px;width:0;height:0;border-left:30px solid transparent;border-right:30px solid transparent;border-top:30px solid var(--white)}

/* gallery */
.filters{top:1436px;left:0;width:1200px;display:flex;justify-content:center;gap:44px;font-size:17px;color:var(--muted)}
.filters .active{color:var(--ink);border-bottom:2px solid var(--orange);padding-bottom:4px}

/* services */
.outline-btn{position:absolute;width:92px;height:34px;line-height:32px;border:1.5px solid var(--orange);color:var(--orange);font-size:12px;text-align:center}

/* testimonial */
.quote{top:3068px;left:436px;width:600px;font-size:19px;line-height:1.68;color:var(--text)}
.quote .mark{color:var(--orange);font-family:"Montserrat",sans-serif;font-weight:700;font-size:30px;line-height:0}
.quote-name{top:3236px;left:456px;font-size:15px;color:var(--muted)}
.clients{top:3196px;left:162px;width:876px;display:flex;justify-content:space-between;align-items:center;margin-top:144px}
.client{font-family:"Montserrat",sans-serif;font-weight:600;font-size:28px;color:var(--client)}

/* subscribe */
.subscribe{top:4202px;left:0;width:1200px;height:286px;background:var(--light)}
.socials{top:68px;left:534px;display:flex;gap:10px}
.socials span{width:14px;height:14px;border-radius:50%;background:var(--ink)}
.sub-title{top:102px;font-size:24px;color:var(--ink)}
.sub-text{top:146px;font-size:13px;color:var(--text)}
.form{top:191px;left:315px;width:567px;height:42px;display:flex}
.form .field{flex:1;background:var(--white);font-size:13px;color:var(--muted);line-height:42px;padding-left:12px}
.form .go{width:100px;background:var(--orange);color:var(--white);font-family:"Montserrat",sans-serif;font-weight:600;font-size:13px;text-align:center;line-height:42px}

/* footer */
.footer{top:4488px;left:0;width:1200px;height:245px;background:var(--footer);color:#bbb}
.footer-brand{left:140px;top:40px;width:220px;text-align:center}
.footer-brand .brand-dot{width:78px;height:78px;margin:0 auto 10px;background:var(--white)}
.footer-brand .name{font-family:"Montserrat",sans-serif;font-weight:700;font-size:20px;color:var(--white);line-height:1;white-space:nowrap}
.footer-brand .name small{display:block;font-size:11px;letter-spacing:5px;margin-top:4px}
.col{top:34px;font-size:11px;line-height:1.75}
.col h4{font-family:"Questrial",sans-serif;font-weight:400;font-size:15px;color:var(--white);margin-bottom:12px}
.col .row{display:flex;gap:8px;align-items:center;margin-bottom:6px}
.col .ico{width:18px;height:18px;border-radius:50%;background:#444;flex:none}
.copy{top:216px;font-size:10px;color:#888}
.footer-bar{top:4733px;left:0;width:1200px;height:42px;background:var(--footer-bar)}
</style>
</head>
<body>

<header class="abs site-nav">
  <div class="abs brand"><span class="brand-dot"></span><span class="brand-name">MAPLE LANTERN<small>PRODUCTIONS</small></span></div>
  <nav class="abs menu"><span>Home</span><span>About Us</span><span>Services</span><span>Events</span><span>Gallery</span><span>Contact Us</span><span class="sep"></span></nav>
  <svg class="abs search" width="18" height="18" viewBox="0 0 18 18"><circle cx="7.5" cy="7.5" r="5.5" fill="none" stroke="#1d1d1d" stroke-width="2.4"/><line x1="11.5" y1="11.5" x2="16" y2="16" stroke="#1d1d1d" stroke-width="2.6"/></svg>
</header>

<section class="abs hero">
  <div class="hero-photo" role="img" aria-label="Bride and groom dancing under blue stage lights at a wedding reception"></div>
  <h1 class="abs center hero-title">MAPLE LANTERN</h1>
  <p class="abs center hero-sub">Sound, lighting, and audio visual services to weddings, corporate.</p>
  <span class="abs btn hero-btn">Get Started</span>
  <svg class="abs arrow" style="left:30px" width="24" height="50" viewBox="0 0 24 50"><polyline points="20,2 4,25 20,48" fill="none" stroke="#fff" stroke-width="3"/></svg>
  <svg class="abs arrow" style="left:1146px" width="24" height="50" viewBox="0 0 24 50"><polyline points="4,2 20,25 4,48" fill="none" stroke="#fff" stroke-width="3"/></svg>
</section>

<section class="intro">
  <h2 class="abs center heading intro-title">Welcome to <span>Maple Lantern</span></h2>
  <p class="abs lead intro-lead">Lorem ipsum dolor sit amet, consectetur adipiscing elit, sed do eiusmod temp or incididunt ut labore et dolore magna aliqut enim ad minim veniam, quis nstrud exercitation ullamco la dolore magna aliunim adboris nis.</p>

  <div class="photo" style="left:162px;top:837px;width:274px;height:188px;background:linear-gradient(135deg,#3a2a6e,#8a5ad0 50%,#2a1a40)" role="img" aria-label="Couple dancing in purple stage lighting"></div>
  <div class="photo" style="left:465px;top:837px;width:273px;height:188px;background:linear-gradient(160deg,#1a1a10,#b7a23a 55%,#5a4a1a)" role="img" aria-label="Reception table lit by string lights"></div>
  <div class="photo" style="left:764px;top:837px;width:274px;height:188px;background:linear-gradient(150deg,#4f6a3a,#2a2a2a 55%,#6e8a50)" role="img" aria-label="Groomsmen celebrating outdoors"></div>

  <h3 class="abs card-title" style="left:162px;top:1042px;width:274px">What We Do</h3>
  <h3 class="abs card-title" style="left:465px;top:1042px;width:273px">Lighting,Sound &amp; Audio visual</h3>
  <h3 class="abs card-title" style="left:764px;top:1042px;width:274px">Who We Are</h3>
  <p class="abs card-text" style="left:170px;top:1076px;width:258px">Lorem ipsum dolor sit amet, consectetur adipiscin sed do eiusmod tempor incididunt ut labore et dolore magna aliqut enim ad minim veniam nostrud.</p>
  <p class="abs card-text" style="left:473px;top:1076px;width:258px">Lorem ipsum dolor sit amet, consectetur adipiscin sed do eiusmod tempor incididunt ut labore et dolore magna aliqut enim ad minim veniam nostrud.</p>
  <p class="abs card-text" style="left:772px;top:1076px;width:258px">Lorem ipsum dolor sit amet, consectetur adipiscin sed do eiusmod tempor incididunt ut labore et dolore magna aliqut enim ad minim veniam nostrud.</p>
</section>

<section class="gallery">
  <div class="abs band" style="top:1194px;background:linear-gradient(90deg,#3a2e2a,#7a6050 50%,#2e2624)" role="img" aria-label="Blurred dance floor at an evening wedding"></div>
  <span class="abs notch" style="top:1194px"></span>
  <h2 class="abs center heading band-title" style="top:1264px">Our Gallery</h2>
  <p class="abs center band-sub" style="top:1326px">Lorem ipsum doloagna aliqut enim ar sit amet</p>

  <div class="abs filters"><span class="active">All</span><span>Weddings</span><span>Corporate</span><span>Lighting</span><span>Sound</span><span>Other</span></div>

  <div class="photo" style="left:162px;top:1499px;width:430px;height:293px;background:linear-gradient(135deg,#e8724a,#c9543a)" role="img" aria-label="Gallery photo with orange hover overlay"></div>
  <svg class="abs" style="left:356px;top:1625px" width="42" height="42" viewBox="0 0 42 42"><circle cx="17" cy="17" r="13" fill="none" stroke="#fff" stroke-width="4"/><line x1="27" y1="27" x2="39" y2="39" stroke="#fff" stroke-width="5"/><line x1="11" y1="17" x2="23" y2="17" stroke="#fff" stroke-width="3"/><line x1="17" y1="11" x2="17" y2="23" stroke="#fff" stroke-width="3"/></svg>
  <div class="photo" style="left:605px;top:1499px;width:433px;height:293px;background:linear-gradient(160deg,#c9b89a,#8a6a5a 55%,#efe6dc)" role="img" aria-label="Couple's first dance in a bright reception hall"></div>
  <div class="photo" style="left:162px;top:1805px;width:210px;height:216px;background:linear-gradient(150deg,#e6ddd2,#a88a76)" role="img" aria-label="Bride and groom embracing"></div>
  <div class="photo" style="left:385px;top:1805px;width:207px;height:216px;background:linear-gradient(150deg,#5a4a9a,#c8a0e0 55%,#3a2a60)" role="img" aria-label="Couple dancing under violet lights"></div>
  <div class="photo" style="left:605px;top:1805px;width:210px;height:216px;background:linear-gradient(150deg,#f0ece4,#b8a89a)" role="img" aria-label="Wedding guests at a reception"></div>
  <div class="photo" style="left:828px;top:1805px;width:210px;height:216px;background:linear-gradient(150deg,#d8b890,#f2e6d6 55%,#b07a50)" role="img" aria-label="Decorated banquet tables"></div>
</section>

<section class="services">
  <div class="abs band" style="top:2088px;background:linear-gradient(90deg,#6a5a50,#3a3030 50%,#8a7060)" role="img" aria-label="Blurred wedding couple in warm light"></div>
  <span class="abs notch" style="top:2088px"></span>
  <h2 class="abs center heading band-title" style="top:2160px">Our Services</h2>
  <p class="abs center band-sub" style="top:2222px">Lorem ipsum doloagna aliqut enim ar sit amet</p>

  <div class="photo" style="left:162px;top:2346px;width:274px;height:185px;background:linear-gradient(170deg,#a8c0d8,#e8e4dc 45%,#7a9a5a)" role="img" aria-label="Outdoor wedding ceremony setup"></div>
  <div class="photo" style="left:465px;top:2346px;width:273px;height:185px;background:linear-gradient(170deg,#d8e0c0,#6a9a3a 55%,#4a7a2a)" role="img" aria-label="Corporate event on a lawn"></div>
  <div class="photo" style="left:764px;top:2346px;width:274px;height:185px;background:linear-gradient(170deg,#d0c8c0,#f4f0ec 55%,#a09890)" role="img" aria-label="Banquet hall with white tables"></div>

  <h3 class="abs card-title" style="left:162px;top:2550px;width:274px;color:#555">Wedding Events</h3>
  <h3 class="abs card-title" style="left:465px;top:2550px;width:273px;color:#555">Corporate Services</h3>
  <h3 class="abs card-title" style="left:764px;top:2550px;width:274px;color:#555">Other Services</h3>
  <p class="abs card-text" style="left:170px;top:2586px;width:258px">Lorem ipsum dolor sit amet, consectetur adipiscin sed do eiusmod tempor incididunt ut labore et dolore magna aliqut enim ad minim veniam nostrud ad eiusmod tempor incididunt ut laborelabore.</p>
  <p class="abs card-text" style="left:473px;top:2586px;width:258px">Lorem ipsum dolor sit amet, consectetur adipiscin sed do eiusmod tempor incididunt ut labore et dolore magna aliqut enim ad minim veniam nostrud ad eiusmod tempor incididunt ut laborelabore.</p>
  <p class="abs card-text" style="left:772px;top:2586px;width:258px">Lorem ipsum dolor sit amet, consectetur adipiscin sed do eiusmod tempor incididunt ut labore et dolore magna aliqut enim ad minim veniam nostrud ad eiusmod tempor incididunt ut laborelabore.</p>
  <span class="outline-btn" style="left:253px;top:2690px">Read More</span>
  <span class="outline-btn" style="left:555px;top:2690px">Read More</span>
  <span class="outline-btn" style="left:855px;top:2690px">Read More</span>
</section>

<section class="testimonials">
  <div class="abs band" style="top:2769px;background:linear-gradient(90deg,#1e1a2a,#3a3050 50%,#1a1620)" role="img" aria-label="Dark event hall backdrop"></div>
  <h2 class="abs center heading band-title" style="top:2840px">Testimonials</h2>
  <p class="abs center band-sub" style="top:2902px">Lorem ipsum doloagna aliqut enim ar sit amet</p>

  <div class="photo" style="left:162px;top:3027px;width:242px;height:242px;border-radius:50%;background:radial-gradient(circle at 40% 40%,#f2ece6,#a89080)" role="img" aria-label="Circular portrait of a wedding couple"></div>
  <p class="abs quote"><span class="mark">&ldquo;</span> Lorem ipsum dolor sit amet, consectetur adipiscing elit, sed do eiu sm od tempor incididunt ut labore et dolore magna aliqut enim ad minim veniam, quis nstrud exercitation ullamco la dolore magna aili loreunim aboris nismpor incididunt ut labore et dolore magna aliqut enim ad minim veniam, quis nstrud exercitatio ladmpor. <span class="mark">&rdquo;</span></p>
  <p class="abs quote-name">Ellis Marrow, City Name</p>

  <div class="abs clients">
    <span class="client">Northwick</span>
    <span class="client">Tallowby</span>
    <span class="client">Brenmoor</span>
    <span class="client">Quillstone</span>
    <span class="client">Ferrowdale</span>
  </div>
</section>

<section class="videos">
  <div class="abs band" style="top:3460px;background:linear-gradient(90deg,#4a4a40,#c8c8bc 50%,#5a5a50)" role="img" aria-label="Banquet hall with set tables"></div>
  <h2 class="abs center heading band-title" style="top:3528px">Featured Videos</h2>
  <p class="abs center band-sub" style="top:3590px">Lorem ipsum doloagna aliqut enim ar sit amet</p>
  <p class="abs lead" style="top:3694px;left:260px;width:680px">Lorem ipsum dolor sit amet, consectetur adipiscing elit, sed do eiusmod temp or incididunt ut labore et dolore magna aliqut enim ad minim veniam, quis nstrud exercitation ullamco la dolore magna aliunim adboris nis.</p>

  <div class="photo" style="left:162px;top:3826px;width:430px;height:293px;background:linear-gradient(150deg,#e8e2d8,#8a6a56 55%,#3a2e2a)" role="img" aria-label="Wedding video thumbnail of a couple"></div>
  <div class="photo" style="left:605px;top:3826px;width:433px;height:293px;background:linear-gradient(150deg,#c8c0b0,#6a5a4a 55%,#2e2a26)" role="img" aria-label="Event video thumbnail of guests dancing"></div>
  <svg class="abs" style="left:347px;top:3942px" width="60" height="60" viewBox="0 0 60 60"><circle cx="30" cy="30" r="28" fill="#1d1d1d" fill-opacity=".8" stroke="#fff" stroke-width="3"/><polygon points="24,18 42,30 24,42" fill="#fff"/></svg>
  <svg class="abs" style="left:791px;top:3942px" width="60" height="60" viewBox="0 0 60 60"><circle cx="30" cy="30" r="28" fill="#1d1d1d" fill-opacity=".8" stroke="#fff" stroke-width="3"/><polygon points="24,18 42,30 24,42" fill="#fff"/></svg>
</section>

<section class="abs subscribe">
  <div class="abs socials"><span></span><span></span><span></span><span></span><span></span><span></span></div>
  <h2 class="abs center sub-title">Subscribe</h2>
  <p class="abs center sub-text">Lorem ipsum dolor sit amet, consectetur adipiscing elit</p>
  <div class="abs form"><span class="field">Email Address</span><span class="go">SIGN UP</span></div>
</section>

<footer class="abs footer">
  <div class="abs footer-brand"><div class="brand-dot"></div><div class="name">MAPLE LANTERN<small>PRODUCTIONS</small></div></div>
  <div class="abs col" style="left:418px;width:200px">
    <h4>Maplelanternco</h4>
    <div class="row"><span class="ico"></span>84 Wexbury Lane, Avon, MA 02417</div>
    <div class="row"><span class="ico"></span>(508) 555-0142</div>
    <div class="row"><span class="ico"></span>(508) 555-0187</div>
    <div class="row"><span class="ico"></span>info@maplelanternco.example</div>
  </div>
  <div class="abs col" style="left:650px;width:140px">
    <h4>Other</h4>
    About Us<br>Delivery Information<br>Privacy Policy<br>Terms &amp; Conditions<br>Blog<br>Careers
  </div>
  <div class="abs col" style="left:822px;width:120px">
    <h4>Events</h4>
    Lorem ipsum<br>sit amet, consectet<br>Weddings all year<br>Corporate nights<br>Lighting and sound<br>Video memories
  </div>
  <div class="abs col" style="left:962px;width:90px">
    <h4>Links</h4>
    Home<br>About Us<br>Services<br>Gallery<br>Contact Us
  </div>
  <p class="abs center copy">Copyright © 2017 Maple Lantern Productions. All Rights Reserved.</p>
</footer>
<div class="abs footer-bar"></div>

</body>
</html>
```